Brookvane Billboard

Please design a billboard using my photos and logos.
For photo of truck please crop the truck itself out and not have the trees / dirt in photo.
Please put " Best Prices in Sevier County"
Please put " 30-yard Dumpsters Starting at 600.00"
Please put " 16-yard Dumpsters Starting at 300.0"
Please put " Delivery and Pickup 7 Days a week"
Billboard size will be 10 ft tall 30 ft wide

```html
<!DOCTYPE html>
<html lang="en">
<head>
<meta charset="UTF-8">
<title>Brookvane Billboard</title>
<link href="https://fonts.googleapis.com/css2?family=Anton&family=Poppins:wght@500;700&display=swap" rel="stylesheet">
<style>
  :root {
    --ink: #0a0a0a;
    --purple: #7b3a98;
    --purple-deep: #5b2a78;
    --white: #ffffff;
    --stage: #e6e6e8;
    --truck-light: #ededf0;
    --truck-mid: #cfcfd6;
    --truck-box: #4e2c74;
  }
  * { margin: 0; padding: 0; box-sizing: border-box; }
  html, body { width: 911px; height: 1200px; overflow: hidden; }
  body { background: var(--stage); position: relative; font-family: "Poppins", sans-serif; }

  .billboard {
    position: absolute;
    left: 25px; top: 457px;
    width: 860px; height: 286px;
    overflow: hidden;
    box-shadow: 0 6px 14px rgba(0,0,0,.25);
  }
  .billboard-bg { position: absolute; inset: 0; width: 100%; height: 100%; }

  .truck-photo {
    position: absolute;
    left: 440px; top: 16px;
    width: 410px; height: 226px;
    border-radius: 14px;
    background: linear-gradient(100deg, var(--truck-mid) 0%, var(--truck-light) 45%, var(--truck-box) 70%, var(--truck-box) 100%);
  }

  .brand {
    position: absolute;
    left: 56px; top: 14px;
    color: var(--white);
    font-weight: 700;
    font-size: 33px;
    line-height: 1.1;
    text-transform: uppercase;
    letter-spacing: 1px;
  }

  .headline {
    position: absolute;
    left: 14px; top: 106px;
    font-family: "Anton", sans-serif;
    font-weight: 400;
    font-size: 40px;
    line-height: 1;
    color: var(--white);
    text-transform: uppercase;
    white-space: nowrap;
    transform: scaleX(.85);
    transform-origin: left center;
  }

  .offers {
    position: absolute;
    left: 15px; top: 151px;
    list-style: none;
    color: var(--white);
    font-weight: 500;
    font-size: 16px;
    line-height: 23px;
    white-space: nowrap;
  }
  .offers li::before {
    content: "\00BB";
    font-weight: 700;
    display: inline-block;
    width: 20px;
  }

  .phone-icon { position: absolute; left: 22px; top: 238px; width: 38px; height: 38px; }
  .phone-number {
    position: absolute;
    left: 72px; top: 229px;
    font-family: "Anton", sans-serif;
    font-size: 46px;
    line-height: 1;
    letter-spacing: 4px;
    color: var(--white);
    white-space: nowrap;
  }

  .web-bar {
    position: absolute;
    left: 626px; top: 251px;
    width: 234px; height: 35px;
    background: var(--ink);
    display: flex; align-items: center; justify-content: center; gap: 6px;
    color: var(--white);
    font-size: 13.5px;
  }
  .web-bar svg { width: 14px; height: 14px; }
</style>
</head>
<body>
  <section class="billboard">
    <svg class="billboard-bg" viewBox="0 0 1490 495" preserveAspectRatio="none" aria-hidden="true">
      <rect width="1490" height="495" fill="var(--ink)"/>
      <rect x="0" y="175" width="820" height="220" fill="var(--purple)"/>
      <polygon points="670,0 785,0 1085,495 985,495" fill="var(--purple)"/>
      <polygon points="735,0 785,0 1085,495 1040,495" fill="var(--purple-deep)"/>
      <polygon points="785,0 1490,0 1490,495 1085,495" fill="var(--white)"/>
    </svg>

    <div class="truck-photo" role="img" aria-label="Photo of a white roll-off truck carrying a purple dumpster"></div>

    <div class="brand">Brookvane<br>Dumpsters</div>

    <h1 class="headline">Best Prices in Sevier County</h1>

    <ul class="offers">
      <li>30-yard Dumpsters Starting at 600.00</li>
      <li>16-yard Dumpsters Starting at 300.0</li>
      <li>Delivery and Pickup 7 Days a week</li>
    </ul>

    <svg class="phone-icon" viewBox="0 0 40 40" aria-hidden="true">
      <circle cx="20" cy="20" r="18" fill="none" stroke="var(--purple)" stroke-width="2.5"/>
      <path d="M13 11 l4 -1 l3 6 l-3 2 q2 5 6 7 l2 -3 l6 3 l-1 4 q-2 2 -5 1 q-9 -3 -13 -13 q-1 -4 1 -6z" fill="var(--purple)"/>
    </svg>
    <div class="phone-number">865-555-0142</div>

    <div class="web-bar">
      <svg viewBox="0 0 20 20" aria-hidden="true">
        <g fill="none" stroke="var(--purple)" stroke-width="1.6">
          <circle cx="10" cy="10" r="8"/>
          <ellipse cx="10" cy="10" rx="3.5" ry="8"/>
          <line x1="2" y1="10" x2="18" y2="10"/>
          <line x1="3.5" y1="6" x2="16.5" y2="6"/>
          <line x1="3.5" y1="14" x2="16.5" y2="14"/>
        </g>
      </svg>
      <span>brookvanedumpsters.com</span>
    </div>
  </section>
</body>
</html>
```